Carwash Signage

We own and operate a 25m tunnel car wash in the uk. We are looking to upgrade our signage to include the following:-

Wash selection Board Size-1300x1300mm
Conditions 1300x1300mm
Instructions 1300x1300mm
Banner 2600x600mm
Stamp card flyer a5 double sided - 9 squares for stamping 3rd square needs to say free air freshener 9th square needs to say free vip car wash.

I have attached some notes for the details that are required to be included.

We are looking for a modern smart look more European car wash style than American car wash style. It should be bold and clear. with yellow/orange & blue/green,grey colours

The final design must be in a industry standard printable format.

UPDATED BRIEF AS DISCUSSED: We require design for 2 x window decals, flag design and 50% off voucher. Attached are rough layout drawings of what they should look like - we expect the designs to be in keeping with the previous designs colours, etc that have been carried out. We Look forward to hearing from you.

Target Market(s)

local car owners within a 15-20 mile radius

Colors
0054AA
0677BA
7BADD7
CADEEF
E8F1F8
0094D4
00A9DD
6FCCEA
C7EBF8
E9F6FB
00AB8E
00BBA5
67D7C9
C6EFE9
E9F9F6

Requirements
Must have
• must be sharp and modern European look

```html
<!DOCTYPE html>
<html lang="nl">
<head>
<meta charset="utf-8">
<title>Harbourline Car Wash – A5 stempelkaart flyer</title>
<link href="https://fonts.googleapis.com/css2?family=Figtree:wght@400;500;600;700;800&family=Montserrat:wght@700;800;900&display=swap" rel="stylesheet">
<style>
  :root{
    --canvas:#b5b5b5;
    --ink:#2b2b2b;
    --royal:#1230b0;
    --navy-band:#1433b3;
    --sky:#1bb0e6;
    --cyan:#00a9dd;
    --blue:#0677ba;
    --teal:#00bba5;
    --tick:#00ab8e;
    --orange:#ff7a1a;
    --paper-top:#eaf6fc;
    --paper-bottom:#c9e7f5;
    --curve-line:#c9d4f0;
    --white:#ffffff;
  }
  *{box-sizing:border-box;margin:0;padding:0}
  html,body{width:1200px;height:851px;overflow:hidden;background:var(--canvas)}
  body{position:relative;font-family:"Figtree",sans-serif;color:var(--ink)}

  /* dimension marks */
  .dim-h{position:absolute;left:80px;top:44px;width:502px;height:0;border-top:1px dashed #333}
  .dim-h span{position:absolute;left:50%;top:-10px;transform:translateX(-50%);background:var(--canvas);padding:0 10px;font-size:15px;white-space:nowrap}
  .dim-v{position:absolute;left:57px;top:74px;width:0;height:712px;border-left:1px dashed #333}
  .dim-v span{position:absolute;left:-10px;top:350px;transform:translate(-50%,-50%) rotate(-90deg);background:var(--canvas);padding:0 10px;font-size:15px;white-space:nowrap}

  /* flyer */
  .flyer{position:absolute;top:74px;width:502px;height:712px;overflow:hidden;
    background:linear-gradient(180deg,var(--paper-top) 0%,#d9eef9 45%,var(--paper-bottom) 80%,#e3f2fa 100%);
    box-shadow:0 14px 30px rgba(0,0,0,.28)}
  .flyer--front{left:80px}
  .flyer--back{left:618px}
  .flyer__curves{position:absolute;inset:0;width:502px;height:712px}

  .brand{position:absolute;top:30px;left:0;width:100%;display:flex;justify-content:center;align-items:center;gap:10px}
  .brand__dot{width:26px;height:26px;border-radius:50%;background:var(--royal)}
  .brand__name{font-family:"Montserrat",sans-serif;font-weight:800;font-size:30px;color:var(--royal);letter-spacing:.5px}

  .tagline{position:absolute;top:108px;width:100%;text-align:center;font-weight:600;font-size:26px;color:var(--sky)}
  .headline{position:absolute;top:138px;width:100%;text-align:center;font-family:"Montserrat",sans-serif;font-weight:900;font-size:72px;letter-spacing:-2px;color:var(--royal);line-height:1}
  .payments{position:absolute;top:212px;width:100%;text-align:center;font-weight:700;font-size:12px;letter-spacing:3px}

  .photo{position:absolute;left:232px;top:222px;width:270px;height:278px;
    background:radial-gradient(ellipse at 60% 55%,#f4f6f8 0%,#cdd8e2 35%,#7fb6dc 60%,rgba(150,200,235,0) 78%)}

  .hours-bar{position:absolute;left:0;top:251px;width:280px;height:24px;
    background:linear-gradient(90deg,var(--cyan) 0%,var(--cyan) 60%,rgba(0,169,221,0) 100%);
    color:var(--white);font-weight:800;font-size:17px;padding-left:38px;line-height:24px}
  .hours{position:absolute;left:38px;top:283px;font-size:16px;font-weight:500;line-height:22px}
  .hours p + p{margin-top:6px}

  .features{position:absolute;left:38px;top:396px;list-style:none;font-size:14px;font-weight:500}
  .features li{display:flex;align-items:center;gap:9px;height:22.5px}
  .features li.cont{padding-left:23px}
  .tick{width:14px;height:14px;flex:none}

  .slogan{position:absolute;width:100%;text-align:center;font-family:"Montserrat",sans-serif;font-weight:800;color:var(--royal);font-size:22px;line-height:22px}
  .flyer--front .slogan{top:595px}
  .flyer--back .slogan{top:614px}
  .address{position:absolute;top:643px;width:100%;text-align:center;font-size:13px;font-weight:500}

  .footer{position:absolute;left:0;top:666px;width:502px;height:46px;background:var(--navy-band)}
  .footer__call{position:absolute;left:0;top:0;width:290px;height:46px;background:var(--orange);
    clip-path:polygon(0 0,262px 0,282px 100%,0 100%);
    color:var(--white);font-weight:600;font-size:20px;line-height:46px;padding-left:37px;display:flex;align-items:center;gap:6px}
  .footer__call svg{width:15px;height:15px}
  .footer__web{position:absolute;left:303px;top:6px;color:var(--white);font-weight:600;font-size:14px;line-height:17px}

  /* back */
  .unlock{position:absolute;top:118px;width:100%;text-align:center;font-family:"Montserrat",sans-serif;font-weight:800;font-size:19.5px;line-height:25px;color:#333}
  .stamps{position:absolute;left:41px;top:184px;display:grid;grid-template-columns:repeat(3,126px);grid-template-rows:repeat(3,129px);column-gap:21px;row-gap:14px}
  .stamp{position:relative;background:var(--white);outline:2px dotted #ffffff;outline-offset:1px;box-shadow:0 0 0 1px #e4eef5}
  .stamp__brand{position:absolute;top:9px;width:100%;display:flex;justify-content:center;align-items:center;gap:4px}
  .stamp__brand i{width:9px;height:9px;border-radius:50%;background:var(--royal)}
  .stamp__brand b{font-family:"Montserrat",sans-serif;font-weight:800;font-size:10px;color:var(--royal)}
  .stamp__panel{position:absolute;left:7px;top:31px;width:112px;height:82px;padding:12px 8px 0;color:var(--white)}
  .stamp__panel--teal{background:var(--teal)}
  .stamp__panel--blue{background:var(--blue)}
  .stamp__panel--cyan{background:var(--cyan)}
  .stamp__title{font-weight:800;font-size:16px;line-height:18px}
  .stamp__text{margin-top:5px;font-size:6px;line-height:9px;width:70px}
  .stamp__badge{position:absolute;right:-3px;bottom:-6px;width:30px;height:30px;border-radius:50%;background:var(--orange);border:1.5px solid var(--white);
    display:flex;flex-direction:column;align-items:center;justify-content:center;color:var(--white);font-weight:800;line-height:1}
  .stamp__badge s{font-size:5.5px;font-weight:600}
  .stamp__badge span{font-size:11px}
  .stamp__badge--free span{font-size:9px}
  .stamp__date{position:absolute;left:8px;bottom:5px;font-size:7px;font-weight:500}
</style>
</head>
<body>

<div class="dim-h"><span>148 mm + 3 mm bleed</span></div>
<div class="dim-v"><span>210 mm + 3 mm bleed</span></div>

<!-- FRONT -->
<section class="flyer flyer--front">
  <svg class="flyer__curves" viewBox="0 0 502 712" aria-hidden="true">
    <path d="M0 0H502V36Q251 152 0 36Z" fill="#f2fbfe"/>
    <path d="M0 36Q251 152 502 36" fill="none" stroke="var(--curve-line)" stroke-width="3"/>
    <path d="M0 597Q251 543 502 597V666H0Z" fill="#e6f4fb"/>
    <path d="M0 597Q251 543 502 597" fill="none" stroke="var(--curve-line)" stroke-width="3"/>
  </svg>

  <div class="brand"><span class="brand__dot"></span><span class="brand__name">HARBOURLINE</span></div>

  <p class="tagline">9x korting op een schone auto!</p>
  <h1 class="headline">CAR WASH</h1>
  <p class="payments">CASH + CARD PAYMENTS ACCEPTED</p>

  <div class="photo" role="img" aria-label="Witte SUV omringd door opspattend water"></div>

  <div class="hours-bar">OPENINGSTIJDEN</div>
  <div class="hours">
    <p>Maandag t/m zaterdag:<br>08:30 - 18:00 uur</p>
    <p>Zon-en feestdagen:<br>9:00 - 16:00 uur</p>
  </div>

  <ul class="features">
    <li><svg class="tick" viewBox="0 0 14 14"><circle cx="7" cy="7" r="7" fill="var(--tick)"/><path d="M5 9.5L9.5 5M6 5H9.5V8.5" stroke="#fff" stroke-width="1.4" fill="none"/></svg>Gratis indoor stofzuigen</li>
    <li><svg class="tick" viewBox="0 0 14 14"><circle cx="7" cy="7" r="7" fill="var(--tick)"/><path d="M5 9.5L9.5 5M6 5H9.5V8.5" stroke="#fff" stroke-width="1.4" fill="none"/></svg>Gratis banden pompen</li>
    <li><svg class="tick" viewBox="0 0 14 14"><circle cx="7" cy="7" r="7" fill="var(--tick)"/><path d="M5 9.5L9.5 5M6 5H9.5V8.5" stroke="#fff" stroke-width="1.4" fill="none"/></svg>Supereffectieve mattenwasser</li>
    <li><svg class="tick" viewBox="0 0 14 14"><circle cx="7" cy="7" r="7" fill="var(--tick)"/><path d="M5 9.5L9.5 5M6 5H9.5V8.5" stroke="#fff" stroke-width="1.4" fill="none"/></svg>Krasvrij wassen</li>
    <li><svg class="tick" viewBox="0 0 14 14"><circle cx="7" cy="7" r="7" fill="var(--tick)"/><path d="M5 9.5L9.5 5M6 5H9.5V8.5" stroke="#fff" stroke-width="1.4" fill="none"/></svg>Velgen reiniging</li>
    <li><svg class="tick" viewBox="0 0 14 14"><circle cx="7" cy="7" r="7" fill="var(--tick)"/><path d="M5 9.5L9.5 5M6 5H9.5V8.5" stroke="#fff" stroke-width="1.4" fill="none"/></svg>Ook geschikt voor bedrijfswagens</li>
    <li class="cont">tot max. 2,05m hoog (zonder imperial)</li>
  </ul>

  <h2 class="slogan">EXPERT TEAM CAR WASHING<br>IN YOUR TOWN</h2>
  <p class="address">Molenweg 14, 6211 AB, Maastricht</p>

  <footer class="footer">
    <div class="footer__call">Call <svg viewBox="0 0 24 24"><path fill="#fff" d="M6.6 10.8a15.1 15.1 0 006.6 6.6l2.2-2.2a1 1 0 011-.25 11.4 11.4 0 003.6.57 1 1 0 011 1V20a1 1 0 01-1 1A17 17 0 013 4a1 1 0 011-1h3.5a1 1 0 011 1c0 1.25.2 2.45.57 3.57a1 1 0 01-.25 1z"/></svg>123 456 7890</div>
    <div class="footer__web">info@websiteurl.com<br>www.websiteurl.com</div>
  </footer>
</section>

<!-- BACK -->
<section class="flyer flyer--back">
  <svg class="flyer__curves" viewBox="0 0 502 712" aria-hidden="true">
    <path d="M0 0H502V36Q251 152 0 36Z" fill="#f2fbfe"/>
    <path d="M0 36Q251 152 502 36" fill="none" stroke="var(--curve-line)" stroke-width="3"/>
  </svg>

  <div class="brand"><span class="brand__dot"></span><span class="brand__name">HARBOURLINE</span></div>

  <h2 class="unlock">UNLOCK A FREE CAR WASH WITH<br>A COMPLETED STAMP CARD</h2>

  <div class="stamps">
    <div class="stamp"><div class="stamp__brand"><i></i><b>HARBOURLINE</b></div>
      <div class="stamp__panel stamp__panel--teal"><p class="stamp__title">REGULAR<br>CAR WASH</p><p class="stamp__text">Lorem ipsum dolor sit amet dummy texts</p><div class="stamp__badge"><s>€16</s><span>€12</span></div></div>
      <p class="stamp__date">Offer till 20 Sept. 2025</p></div>
    <div class="stamp"><div class="stamp__brand"><i></i><b>HARBOURLINE</b></div>
      <div class="stamp__panel stamp__panel--blue"><p class="stamp__title">REGULAR<br>CAR WASH</p><p class="stamp__text">Lorem ipsum dolor sit amet dummy texts</p><div class="stamp__badge"><s>€16</s><span>€12</span></div></div>
      <p class="stamp__date">Offer till 20 Sept. 2025</p></div>
    <div class="stamp"><div class="stamp__brand"><i></i><b>HARBOURLINE</b></div>
      <div class="stamp__panel stamp__panel--cyan"><p class="stamp__title">AIR<br>FRESHENER</p><p class="stamp__text">Lorem ipsum dolor sit amet dummy texts</p><div class="stamp__badge stamp__badge--free"><span>FREE</span></div></div>
      <p class="stamp__date">Offer till 20 Sept. 2025</p></div>

    <div class="stamp"><div class="stamp__brand"><i></i><b>HARBOURLINE</b></div>
      <div class="stamp__panel stamp__panel--blue"><p class="stamp__title">REGULAR<br>CAR WASH</p><p class="stamp__text">Lorem ipsum dolor sit amet dummy texts</p><div class="stamp__badge"><s>€16</s><span>€12</span></div></div>
      <p class="stamp__date">Offer till 20 Sept. 2025</p></div>
    <div class="stamp"><div class="stamp__brand"><i></i><b>HARBOURLINE</b></div>
      <div class="stamp__panel stamp__panel--teal"><p class="stamp__title">REGULAR<br>CAR WASH</p><p class="stamp__text">Lorem ipsum dolor sit amet dummy texts</p><div class="stamp__badge"><s>€16</s><span>€12</span></div></div>
      <p class="stamp__date">Offer till 20 Sept. 2025</p></div>
    <div class="stamp"><div class="stamp__brand"><i></i><b>HARBOURLINE</b></div>
      <div class="stamp__panel stamp__panel--blue"><p class="stamp__title">REGULAR<br>CAR WASH</p><p class="stamp__text">Lorem ipsum dolor sit amet dummy texts</p><div class="stamp__badge"><s>€16</s><span>€12</span></div></div>
      <p class="stamp__date">Offer till 20 Sept. 2025</p></div>

    <div class="stamp"><div class="stamp__brand"><i></i><b>HARBOURLINE</b></div>
      <div class="stamp__panel stamp__panel--cyan"><p class="stamp__title">REGULAR<br>CAR WASH</p><p class="stamp__text">Lorem ipsum dolor sit amet dummy texts</p><div class="stamp__badge"><s>€16</s><span>€12</span></div></div>
      <p class="stamp__date">Offer till 20 Sept. 2025</p></div>
    <div class="stamp"><div class="stamp__brand"><i></i><b>HARBOURLINE</b></div>
      <div class="stamp__panel stamp__panel--blue"><p class="stamp__title">REGULAR<br>CAR WASH</p><p class="stamp__text">Lorem ipsum dolor sit amet dummy texts</p><div class="stamp__badge"><s>€16</s><span>€12</span></div></div>
      <p class="stamp__date">Offer till 20 Sept. 2025</p></div>
    <div class="stamp"><div class="stamp__brand"><i></i><b>HARBOURLINE</b></div>
      <div class="stamp__panel stamp__panel--teal"><p class="stamp__title">VIP CAR<br>WASH</p><p class="stamp__text">Lorem ipsum dolor sit amet dummy texts</p><div class="stamp__badge stamp__badge--free"><span>FREE</span></div></div>
      <p class="stamp__date">Offer till 20 Sept. 2025</p></div>
  </div>

  <h2 class="slogan">EXPERT TEAM CAR WASHING</h2>
  <p class="address">Molenweg 14, 6211 AB, Maastricht</p>

  <footer class="footer">
    <div class="footer__call">Call <svg viewBox="0 0 24 24"><path fill="#fff" d="M6.6 10.8a15.1 15.1 0 006.6 6.6l2.2-2.2a1 1 0 011-.25 11.4 11.4 0 003.6.57 1 1 0 011 1V20a1 1 0 01-1 1A17 17 0 013 4a1 1 0 011-1h3.5a1 1 0 011 1c0 1.25.2 2.45.57 3.57a1 1 0 01-.25 1z"/></svg>123 456 7890</div>
    <div class="footer__web">info@websiteurl.com<br>www.websiteurl.com</div>
  </footer>
</section>

</body>
</html>
```